Hardcore nerd needs to stand out in a sea of dull Defence business cards

Wombarra Devices is a new Australian consulting engineering company that turns research and theory into practical systems. No evangelistic fluff, just mathematics and physics into electronic and optical circuits for consumer products, scientific research or Defence applications.

We already have a recognised logo (provided) which is often dark blue/black on a light background but we're open to other combinations. (Us engineers tend to have limited aesthetic imagination :)

Some of our recent products have included:
* Instrumentation for electrical testing,
* Radar jammers,
* GPS antenna design,
* Satellite tracking systems,
* High power lasers

We're open to both single and double-sided designs - happy to be convinced either way.

P.S. Another group is working on the web page, so - alas - our web site is currently of no use for images/ideas...

Target Market(s)

Engineering managers,
Scientists

Contact Information for Business Card

Dr Colin Harte
R&D Engineer

colin@wombarradevices.com.au
0427 563 710

PO Box XXX (to be confirmed)
Kelsby ACT 2917
Australia

Font styles to use
Serif
Sans Serif

Colors

Designer to choose colors to be used in the design.

Requirements
Must have
• My contact details!
• I've had many (great) "bold and plain" designs submitted already, so feel free to be artistically creative :)
• Happy to take advice re fonts/colours/printability etc.
Nice to have
• I'm not sure if "lists" are more at home on a CV than a business card, but representative services include:
• Applied electromagnetics
• RF and high speed electronics
• Signal and image processing
• Electro-optical and laser systems
• Concept-to-prototype design services
• If you're considering double sided cards, then often measuring/alignment grids/rulers feature on the back of similar cards.
• e.g. https://www.veltranoptics.example/newgrouppage9.cfm?objectgroup_id=4183
• https://www.veltranoptics.example/newgrouppage9.cfm?objectgroup_ID=4185
• ..or even a "Smith chart" (google will return lots)
• Generic images to represent a capability might work - googling images associated with keyword for each of these areas might help:
• - "passive radar", "phased array", "fdtd", "vircator"
• RF and high speed electronic design
• - "smith chart", "microstrip circuits", "dimensioned drawing", "electronic schematic"
• - "dft", "iir filter"
• - "optical cavity". "laser energy level diagram"
• Background/watermarked images outlines/wireframes/schematics would probably look OK.
Should not have
• If a list of projects/services is provided, it is important not to make the client feel that this is "all" the company can do. Engineering design is a creative discipline (like graphics :)
• Please, no stock "military" snaps like planes, missiles, etc!

```html
<!DOCTYPE html>
<html lang="en">
<head>
<meta charset="utf-8">
<title>Wombarra Devices – Business Card</title>
<link rel="stylesheet" href="https://fonts.googleapis.com/css2?family=Arimo:wght@400;700&display=swap">
<style>
  :root {
    --card-white: #ffffff;
    --ink-black: #0d0a0a;
    --brand-red: #be1622;
    --text-grey: #5b5b5b;
    --rule-grey: #9a9a9a;
  }
  * { margin: 0; padding: 0; box-sizing: border-box; }
  html, body {
    width: 1200px;
    height: 720px;
    overflow: hidden;
    background: var(--card-white);
  }
  .card {
    position: relative;
    width: 1200px;
    height: 720px;
    background: var(--card-white);
    font-family: "Arimo", Arial, sans-serif;
    overflow: hidden;
  }
  .brand {
    position: absolute;
    left: 113px;
    top: 284px;
    display: flex;
    align-items: center;
    gap: 22px;
  }
  .brand-dot {
    width: 124px;
    height: 124px;
    border-radius: 50%;
    background: var(--ink-black);
    flex: none;
  }
  .brand-name {
    color: var(--ink-black);
    font-weight: 700;
    line-height: 1.05;
  }
  .brand-name .line-main { display: block; font-size: 44px; letter-spacing: 0.5px; }
  .brand-name .line-sub { display: block; font-size: 27px; letter-spacing: 6px; margin-top: 6px; }
  .divider {
    position: absolute;
    left: 577px;
    top: 194px;
    width: 2px;
    height: 330px;
    background: var(--rule-grey);
  }
  .details {
    position: absolute;
    left: 624px;
    top: 190px;
    color: var(--text-grey);
  }
  .person-name {
    color: var(--brand-red);
    font-size: 43px;
    font-weight: 400;
    line-height: 1.1;
  }
  .person-role {
    font-size: 28px;
    margin-top: 4px;
  }
  .postal {
    font-size: 28px;
    line-height: 1.4;
    margin-top: 36px;
  }
  .contacts {
    list-style: none;
    margin-top: 24px;
    font-size: 27px;
  }
  .contacts li {
    display: flex;
    align-items: center;
    height: 39px;
  }
  .contacts svg {
    width: 22px;
    height: 22px;
    margin-right: 24px;
    flex: none;
    fill: none;
    stroke: var(--brand-red);
    stroke-width: 2;
  }
  .footer-bands {
    position: absolute;
    left: 0;
    bottom: 0;
    width: 1200px;
    height: 64px;
  }
</style>
</head>
<body>
  <main class="card">
    <div class="brand">
      <span class="brand-dot" aria-hidden="true"></span>
      <span class="brand-name">
        <span class="line-main">WOMBARRA</span>
        <span class="line-sub">DEVICES</span>
      </span>
    </div>

    <div class="divider" aria-hidden="true"></div>

    <section class="details">
      <h1 class="person-name">Dr Colin Harte</h1>
      <p class="person-role">R&amp;D Engineer</p>
      <p class="postal">PO Box XXX Kelsby ACT 2917<br>Australia</p>
      <ul class="contacts">
        <li>
          <svg viewBox="0 0 24 24" aria-hidden="true"><path d="M6 3l4 4-2 3c1.5 3 3 4.5 6 6l3-2 4 4-3 3C10 20 4 14 3 6z"/><path d="M14 4a6 6 0 0 1 6 6M14 8a2 2 0 0 1 2 2"/></svg>
          0427 563 710
        </li>
        <li>
          <svg viewBox="0 0 24 24" aria-hidden="true"><rect x="3" y="8" width="18" height="13"/><path d="M3 8l9 7 9-7M7 8V3h10v5"/></svg>
          colin@wombarradevices.com.au
        </li>
        <li>
          <svg viewBox="0 0 24 24" aria-hidden="true"><circle cx="12" cy="12" r="9"/><ellipse cx="12" cy="12" rx="4" ry="9"/><path d="M3 12h18"/></svg>
          www.veltranoptics.example
        </li>
      </ul>
    </section>

    <svg class="footer-bands" viewBox="0 0 1200 64" aria-hidden="true">
      <polygon points="0,30 536,30 502,64 0,64" fill="var(--brand-red)"/>
      <polygon points="573,0 1200,0 1200,64 514,64" fill="var(--ink-black)"/>
    </svg>
  </main>
</body>
</html>
```